Harbor Crestline (Business Card Design)

Need business cards designed. Something modern, chic, and sleek. Mabye the back of the card should be the navy blue that is in the logo and then just the logo on the back.

Target Market(s)

Those in the hotel, office, and renovation industry

Contact Information for Business Card

1. Logo 2. Dorian Fenwick 3. CEO/Founder 4. Phone: (833) HarbCre / (833) 427-2731 5. Email: dorian@theharborcrestline.com 6. Website: www.theharborcrestline.com

Font styles to use
Other font styles liked:
• Look at the logo font and base the font for everything else off of that.

Colors
0054AA
0677BA
7BADD7
CADEEF
E8F1F8

Requirements
Must have
• Colors that are associated in the logo
Nice to have
• Sleek modern clean and chic design.

```html
<!DOCTYPE html>
<html lang="en">
<head>
<meta charset="utf-8">
<title>Harbor Crestline — Business Card</title>
<link rel="stylesheet" href="https://fonts.googleapis.com/css2?family=Montserrat:wght@600&family=Poppins:wght@400;500;700&display=swap">
<style>
  :root {
    --navy: #101a45;
    --navy-glow: #263468;
    --gold: #d9a531;
    --white: #ffffff;
    --page: #ffffff;
    --divider: rgba(255, 255, 255, 0.35);
  }
  * { box-sizing: border-box; margin: 0; padding: 0; }
  html, body {
    width: 1200px; height: 1087px; overflow: hidden;
    background: var(--page);
  }
  .sheet {
    width: 1200px; height: 1087px;
    display: flex; flex-direction: column; align-items: center; justify-content: center;
    gap: 40px;
  }
  .card {
    position: relative;
    width: 860px; height: 491px;
    box-shadow: 0 2px 6px rgba(0, 0, 0, 0.25);
    overflow: hidden;
  }
  .card-surface {
    position: absolute; inset: 0;
    background: radial-gradient(circle at 50% 42%, var(--navy-glow) 0%, var(--navy) 45%, var(--navy) 100%);
  }
  .card-info .card-surface {
    background: radial-gradient(circle at 22% 45%, #1c2858 0%, var(--navy) 40%, var(--navy) 100%);
  }

  /* Brand name block */
  .brand {
    position: absolute;
    display: flex; flex-direction: column; align-items: center;
    font-family: "Montserrat", sans-serif; font-weight: 600;
    color: var(--white); text-transform: uppercase; text-align: center;
  }
  .brand-mark { background: var(--gold); }
  .card-back .brand {
    left: 0; right: 0; top: 150px; gap: 30px;
    font-size: 48px; letter-spacing: 5px; line-height: 1.15;
  }
  .card-back .brand-mark { width: 26px; height: 26px; }
  .card-info .brand {
    left: 40px; width: 300px; top: 168px; gap: 22px;
    font-size: 28px; letter-spacing: 3px; line-height: 1.2;
  }
  .card-info .brand-mark { width: 16px; height: 16px; }

  /* Contact block */
  .divider {
    position: absolute; left: 362px; top: 128px;
    width: 1px; height: 236px; background: var(--divider);
  }
  .contact {
    position: absolute; left: 400px; top: 136px;
    font-family: "Poppins", sans-serif; color: var(--white);
  }
  .contact-name { font-size: 29px; font-weight: 700; color: var(--gold); line-height: 1.2; }
  .contact-role { font-size: 21px; font-weight: 500; margin-top: 4px; }
  .contact-rule { width: 210px; height: 2px; background: var(--gold); margin: 10px 0 18px; }
  .contact-list { list-style: none; font-size: 15.5px; font-weight: 400; }
  .contact-list li { height: 34px; line-height: 34px; }
</style>
</head>
<body>
<main class="sheet">
  <section class="card card-back" aria-label="Card back">
    <div class="card-surface" role="img" aria-label="Navy background with faint diamond pattern"></div>
    <div class="brand">
      <span class="brand-mark"></span>
      <span class="brand-name">Harbor<br>Crestline</span>
    </div>
  </section>

  <section class="card card-info" aria-label="Card front">
    <div class="card-surface" role="img" aria-label="Navy background with faint diamond pattern"></div>
    <div class="brand">
      <span class="brand-mark"></span>
      <span class="brand-name">Harbor<br>Crestline</span>
    </div>
    <div class="divider"></div>
    <div class="contact">
      <p class="contact-name">Dorian Fenwick</p>
      <p class="contact-role">CEO/Founder</p>
      <div class="contact-rule"></div>
      <ul class="contact-list">
        <li>(833) HarbCre</li>
        <li>(833) 427-2731</li>
        <li>dorian@theharborcrestline.com</li>
        <li>www.theharborcrestline.com</li>
      </ul>
    </div>
  </section>
</main>
</body>
</html>
```